Hardcore nerd needs to stand out in a sea of dull Defence business cards

Wombarra Devices is a new Australian consulting engineering company that turns research and theory into practical systems. No evangelistic fluff, just mathematics and physics into electronic and optical circuits for consumer products, scientific research or Defence applications.

We already have a recognised logo (provided) which is often dark blue/black on a light background but we're open to other combinations. (Us engineers tend to have limited aesthetic imagination :)

Some of our recent products have included:
* Instrumentation for electrical testing,
* Radar jammers,
* GPS antenna design,
* Satellite tracking systems,
* High power lasers

We're open to both single and double-sided designs - happy to be convinced either way.

P.S. Another group is working on the web page, so - alas - our web site is currently of no use for images/ideas...

Target Market(s)

Engineering managers,
Scientists

Contact Information for Business Card

Dr Colin Harte
R&D Engineer

colin@wombarradevices.com.au
0427 563 710

PO Box XXX (to be confirmed)
Kelsby ACT 2917
Australia

Font styles to use
Serif
Sans Serif

Colors

Designer to choose colors to be used in the design.

Requirements
Must have
• My contact details!
• I've had many (great) "bold and plain" designs submitted already, so feel free to be artistically creative :)
• Happy to take advice re fonts/colours/printability etc.
Nice to have
• I'm not sure if "lists" are more at home on a CV than a business card, but representative services include:
• Applied electromagnetics
• RF and high speed electronics
• Signal and image processing
• Electro-optical and laser systems
• Concept-to-prototype design services
• If you're considering double sided cards, then often measuring/alignment grids/rulers feature on the back of similar cards.
• e.g. https://www.veltranoptics.example/newgrouppage9.cfm?objectgroup_id=4183
• https://www.veltranoptics.example/newgrouppage9.cfm?objectgroup_ID=4185
• ..or even a "Smith chart" (google will return lots)
• Generic images to represent a capability might work - googling images associated with keyword for each of these areas might help:
• - "passive radar", "phased array", "fdtd", "vircator"
• RF and high speed electronic design
• - "smith chart", "microstrip circuits", "dimensioned drawing", "electronic schematic"
• - "dft", "iir filter"
• - "optical cavity". "laser energy level diagram"
• Background/watermarked images outlines/wireframes/schematics would probably look OK.
Should not have
• If a list of projects/services is provided, it is important not to make the client feel that this is "all" the company can do. Engineering design is a creative discipline (like graphics :)
• Please, no stock "military" snaps like planes, missiles, etc!

```html
<!DOCTYPE html>
<html lang="en">
<head>
<meta charset="utf-8">
<title>Wombarra Devices – Business Card</title>
<link rel="stylesheet" href="https://fonts.googleapis.com/css2?family=Open+Sans:wght@700;800&family=Arimo:wght@400;700&display=swap">
<style>
  :root {
    --navy: #232c6e;
    --navy-deep: #1c2460;
    --ink-grey: #6b6e78;
    --paper: #ffffff;
    --backdrop: #e7e8ec;
  }
  * { box-sizing: border-box; margin: 0; padding: 0; }
  html, body { width: 1200px; height: 900px; overflow: hidden; }
  body {
    background: var(--backdrop);
    font-family: "Arimo", Arial, sans-serif;
    display: flex;
    flex-direction: column;
    align-items: center;
    justify-content: center;
    gap: 26px;
  }
  .card {
    position: relative;
    width: 720px;
    height: 411px;
    overflow: hidden;
    box-shadow: 0 6px 18px rgba(0,0,0,0.18);
  }

  /* Front */
  .card-front { background: var(--paper); }
  .front-swoosh { position: absolute; inset: 0; width: 100%; height: 100%; }
  .front-details { position: absolute; left: 42px; top: 34px; color: var(--navy); }
  .wordmark {
    font-family: "Open Sans", Arial, sans-serif;
    font-weight: 800;
    font-size: 25px;
    letter-spacing: 0.5px;
    line-height: 1.1;
    text-transform: uppercase;
    color: var(--navy);
  }
  .person { margin-top: 22px; }
  .person-name { font-weight: 700; font-size: 19px; text-transform: uppercase; }
  .person-role { font-size: 14px; color: var(--ink-grey); margin-top: 2px; }
  .contact-list { list-style: none; margin-top: 16px; }
  .contact-list li {
    display: flex; align-items: center; gap: 9px;
    font-size: 14px; color: var(--ink-grey); line-height: 22px;
  }
  .contact-list svg { width: 14px; height: 14px; flex: none; }
  .postal { margin-top: 18px; font-size: 14px; line-height: 20px; color: var(--ink-grey); }

  /* Back */
  .card-back { background: var(--navy); color: var(--paper); }
  .back-brand {
    position: absolute; left: 340px; top: 120px;
    display: flex; align-items: center; gap: 14px;
  }
  .back-brand .wordmark { color: var(--paper); font-size: 27px; }
  .brand-dot { width: 40px; height: 40px; border-radius: 50%; background: var(--paper); }
  .services {
    position: absolute; left: 28px; top: 230px; right: 28px;
    list-style: none; display: flex; flex-wrap: wrap; column-gap: 14px; row-gap: 6px;
    font-size: 14.5px;
  }
  .services li::before { content: "\25AA"; margin-right: 4px; }
  .services .break { flex-basis: 100%; height: 0; }
  .services .break::before { content: none; }
</style>
</head>
<body>

<section class="card card-front" aria-label="Card front">
  <svg class="front-swoosh" viewBox="0 0 720 411" aria-hidden="true">
    <path d="M250 411 A330 330 0 0 1 720 130 L720 411 Z" fill="var(--navy)"/>
    <path d="M232 330 A345 345 0 0 1 610 110" fill="none" stroke="var(--navy)" stroke-width="7" stroke-linecap="round"/>
  </svg>

  <div class="front-details">
    <div class="wordmark">Wombarra<br>Devices</div>
    <div class="person">
      <div class="person-name">Dr Colin Harte</div>
      <div class="person-role">R&amp;D Engineer</div>
    </div>
    <ul class="contact-list">
      <li>
        <svg viewBox="0 0 16 16"><circle cx="8" cy="8" r="7" fill="none" stroke="var(--navy)" stroke-width="1.4"/><path d="M5.5 4.5l1.4 1.6-.8 1c.5 1 1.3 1.8 2.3 2.3l1-.8 1.6 1.4-.8 1.3c-2.6-.4-4.7-2.5-5.1-5.1z" fill="var(--navy)"/></svg>
        0427 563 710
      </li>
      <li>
        <svg viewBox="0 0 16 16"><rect x="1.5" y="3.5" width="13" height="9" fill="none" stroke="var(--navy)" stroke-width="1.4"/><path d="M1.5 3.5L8 9l6.5-5.5" fill="none" stroke="var(--navy)" stroke-width="1.4"/></svg>
        colin@wombarradevices.com.au
      </li>
      <li>
        <svg viewBox="0 0 16 16"><circle cx="8" cy="8" r="7" fill="var(--navy)"/><path d="M1 8h14M8 1c-3 3.5-3 10.5 0 14M8 1c3 3.5 3 10.5 0 14" fill="none" stroke="#fff" stroke-width="1"/></svg>
        www.wombarradevices.com.au
      </li>
    </ul>
    <div class="postal">PO Box XXX<br>Kelsby ACT 2917, Australia</div>
  </div>
</section>

<section class="card card-back" aria-label="Card back">
  <div class="back-brand">
    <span class="brand-dot"></span>
    <span class="wordmark">Wombarra Devices</span>
  </div>
  <ul class="services">
    <li>Applied electromagnetics</li>
    <li>RF and high speed electronics</li>
    <li>Signal and image processing</li>
    <li class="break"></li>
    <li>Electro-optical and laser systems</li>
    <li>Concept-to-prototype design services</li>
  </ul>
</section>

</body>
</html>
```